Institutional website for an IT Consulting company

Web design + HTML + CSS / Bootstrap + JS (interaction) integration in order to extend our existing website brightvale.coop.
Our website is currently aiming only for recruitment and not for customers, we want to provide a fluid transition between customer side website (this project) and recruitment website (existing site).

Ideally we would love the new design to be "inspired" by our actual graphic chart (Colors mainly). It should provide a great user experience and a landing page (or any mean) allowing the visitor to easily switch from the end customer front end (this project), the recruitment front end (existing front end https://www.brightvale.coop/) and the existing member front end (an other existing front end dedicated to members already existing).

In attachment you will find the expected site content mainly a one page with a first level of information and "link" to sub pages (a way to directly access this sub pages should also be provided).

The website should be accessible on mobile device and desktop.

The attachment is in french as it reflect the final site content, but if google translate isn't sufficient to have a general idea of the content, feel free to ask. We would love to have some visual representation for some categories.

Target Market(s)

fortune 500 companies

Industry/Entity Type

It Company

Coding

Coded - Design and coding required

Number of Pages Required

5+ page

Requirements
Must have
• This project must have an easy way to navigate between 3 sub sites, the customer one (the one designed here), the consultant / recruitment one (the existing one at brightvale.coop), the members one.

A one page experience at first leading to detail pages.

Custom made visuals to illustrate each categories.

Inspiration websites : pirog[.]fr ; tasklynn[.]com ; dorvelo[.] com ...

Be inspired by the existing color from our logo and existing website at brightvale[.]coop

```html
<!DOCTYPE html>
<html lang="en">
<head>
<meta charset="utf-8">
<title>BRIGHTVALE.COOP – IT consulting for enterprises</title>
<link rel="stylesheet" href="https://fonts.googleapis.com/css2?family=Rubik:wght@400;500;700&display=swap">
<style>
:root{
  --teal:#1aa7b4;
  --teal-dark:#0c3b3a;
  --who:#245e5c;
  --ink:#1f2d2d;
  --grey:#6b7475;
  --light:#f4f5f5;
  --footer:#242424;
  --white:#ffffff;
}
*{box-sizing:border-box;margin:0;padding:0}
html,body{width:1200px;height:3194px;overflow:hidden}
body{position:relative;font-family:'Rubik',sans-serif;color:var(--ink);background:var(--white)}
a{text-decoration:none;color:inherit}
.abs{position:absolute}
.btn{position:absolute;height:48px;display:flex;align-items:center;justify-content:center;gap:10px;font-weight:500;font-size:17px;letter-spacing:.3px;color:var(--white);text-transform:uppercase;white-space:nowrap}
.btn svg{width:15px;height:15px}
.btn--dark{background:var(--teal-dark)}
.btn--teal{background:var(--teal)}
.btn--outline{border:3px solid var(--white);background:transparent}
.btn--outline-dark{border:3px solid var(--teal-dark);background:var(--white);color:var(--teal-dark)}

/* hero */
.hero{top:0;left:0;width:1200px;height:749px;background:linear-gradient(115deg,#eef0ee 0%,#d9c2a0 28%,#8a8f94 55%,#4d5f6e 80%,#3d4c5b 100%)}
.brand{position:absolute;font-weight:700;color:var(--teal-dark);letter-spacing:1px;line-height:1}
.brand--top{left:143px;top:38px;font-size:44px}
.brand small{display:block;text-align:right;font-size:17px;margin-top:2px}

/* sub-site switch */
.site-switch{position:absolute;top:50px;right:145px;display:flex;gap:22px;font-size:15px;font-weight:500;color:var(--teal-dark);white-space:nowrap}
.site-switch a{padding:0 5px 20px;border-bottom:3px solid transparent}
.site-switch a.is-current{border-color:var(--teal)}

.hero__title{left:0;width:1200px;top:290px;text-align:center;font-size:84px;font-weight:700;color:var(--white);letter-spacing:2px;line-height:1}
.hero__lead{left:0;width:1200px;top:414px;text-align:center;font-size:21px;font-weight:500;line-height:34px;color:var(--white)}
.dots{left:551px;top:675px;display:flex;gap:7px}
.dots span{width:14px;height:14px;border-radius:50%;background:var(--white)}
.dots span.on{background:transparent;border:3px solid var(--white)}

/* band */
.band{top:749px;left:0;width:1200px;height:126px;background:var(--teal)}
.band h2{position:absolute;left:143px;top:45px;font-size:34px;line-height:1;font-weight:700;color:var(--white);letter-spacing:.5px}

/* benefits */
.benefits{top:875px;left:0;width:1200px;height:980px;background:var(--light)}
.section-title{position:absolute;left:0;width:1200px;text-align:center;font-size:40px;line-height:1;font-weight:700;color:var(--ink)}
.benefits .section-title{top:110px}
.benefit{position:absolute;width:280px;text-align:center}
.benefit__art{width:159px;height:134px;margin:0 auto;border:3px solid var(--teal);background:linear-gradient(180deg,#ffffff,#e9f6f7)}
.benefit p{margin-top:50px;font-size:17px;line-height:25px;color:#3c4546;font-weight:500}

/* who */
.who{top:1855px;left:0;width:1200px;height:511px;background:linear-gradient(90deg,var(--who),#2b6a68 60%,#1e4f4e)}
.who h2{position:absolute;left:146px;top:90px;font-size:40px;line-height:1;font-weight:700;color:var(--white)}
.who__text{position:absolute;left:143px;top:172px;width:410px;font-size:15.5px;line-height:28px;color:#e3eeee}
.who__text p+p{margin-top:14px}
.video{position:absolute;left:595px;top:81px;width:460px;height:349px;border:5px solid var(--teal);background:linear-gradient(180deg,#fafafa,#eef3f3)}
.video .play{position:absolute;left:192px;top:135px}

/* contact */
.contact{top:2366px;left:0;width:1200px;height:715px;background:var(--white)}
.contact .section-title{top:105px}
.contact h3{position:absolute;top:228px;font-size:25px;line-height:1;font-weight:700;color:var(--teal-dark);letter-spacing:.5px}
.note{position:absolute;font-size:15px;color:var(--grey)}
.field{position:absolute;left:144px;width:357px;border:1px solid #cfd4d4;background:var(--white);font-size:14px;color:#4c5455;padding:16px 25px}
.info{position:absolute;left:651px;font-size:15.5px;color:var(--grey);line-height:28px}
.info svg{width:13px;height:13px;vertical-align:-1px;margin-right:6px}
.map{position:absolute;left:651px;top:376px;width:406px;height:245px;border:1px solid #d6d6d6;background:linear-gradient(135deg,#f1efe9,#e6e4dc 60%,#ecebe4)}

/* footer */
.footer{top:3081px;left:0;width:1200px;height:113px;background:var(--footer)}
.brand--foot{left:143px;top:30px;font-size:40px;color:var(--white)}
.brand--foot small{font-size:16px}
.copy{position:absolute;left:470px;top:48px;font-size:15px;color:var(--white)}
.social{position:absolute;top:37px;display:flex;gap:7px;left:929px}
.social span{width:38px;height:38px;border-radius:50%;background:var(--teal)}
</style>
</head>
<body>

<header class="abs hero">
  <div role="img" aria-label="Photo of hands reviewing business charts with digital data overlay" class="abs" style="inset:0"></div>
  <div class="brand brand--top">BRIGHTVALE<small>.COOP</small></div>
  <nav class="site-switch" aria-label="Switch site">
    <a class="is-current" href="#">FOR CLIENTS</a>
    <a href="https://www.brightvale.coop/">FOR CONSULTANTS</a>
    <a href="#">MEMBER AREA</a>
  </nav>
  <h1 class="abs hero__title">BRIGHTVALE.COOP</h1>
  <p class="abs hero__lead">BRIGHTVALE.COOP is a cooperative of IT experts delivering<br>digital services to large companies.</p>
  <a class="btn btn--dark" style="left:413px;top:526px;width:181px">Contact us <svg viewBox="0 0 16 16"><circle cx="8" cy="8" r="8" fill="#fff"/><path d="M6.5 4.5 10 8l-3.5 3.5" stroke="#0c3b3a" stroke-width="2.2" fill="none"/></svg></a>
  <a class="btn btn--teal" style="left:606px;top:526px;width:183px">Watch video <svg viewBox="0 0 16 16"><circle cx="8" cy="8" r="8" fill="#fff"/><path d="M6.5 4.5 10 8l-3.5 3.5" stroke="#1aa7b4" stroke-width="2.2" fill="none"/></svg></a>
  <div class="abs dots"><span></span><span></span><span class="on"></span><span></span><span></span></div>
</header>

<section class="abs band">
  <h2>FIND THE RIGHT EXPERT</h2>
  <a class="btn btn--dark" style="left:680px;top:39px;width:181px">Contact us <svg viewBox="0 0 16 16"><circle cx="8" cy="8" r="8" fill="#fff"/><path d="M6.5 4.5 10 8l-3.5 3.5" stroke="#0c3b3a" stroke-width="2.2" fill="none"/></svg></a>
  <a class="btn btn--outline" style="left:874px;top:39px;width:181px">Read more <svg viewBox="0 0 16 16"><circle cx="8" cy="8" r="8" fill="#fff"/><path d="M6.5 4.5 10 8l-3.5 3.5" stroke="#1aa7b4" stroke-width="2.2" fill="none"/></svg></a>
</section>

<section class="abs benefits">
  <h2 class="section-title">WHY WORK WITH US?</h2>
  <div class="benefit" style="left:117px;top:237px"><div class="benefit__art" role="img" aria-label="Sketch of two figures and a heart"></div><p>Senior experts who are<br>partners in the company,<br>not subcontractors.</p></div>
  <div class="benefit" style="left:454px;top:237px"><div class="benefit__art" role="img" aria-label="Sketch of a group under a dome"></div><p>A transparent way of working<br>based on the principle<br>of social and solidarity<br>responsibility.</p></div>
  <div class="benefit" style="left:790px;top:237px"><div class="benefit__art" role="img" aria-label="Sketch of a figure balancing on a line"></div><p>A cooperative legal<br>framework that secures<br>your contracts while keeping<br>the agility of<br>independent experts.</p></div>
  <div class="benefit" style="left:117px;top:596px"><div class="benefit__art" role="img" aria-label="Sketch of figures sharing ideas"></div><p>Shared knowledge and<br>mutual aid within a group<br>of recognized experts in<br>their field.</p></div>
  <div class="benefit" style="left:454px;top:596px"><div class="benefit__art" role="img" aria-label="Sketch of a building and a new business idea"></div><p>A fair alternative to the<br>margins and layers of<br>traditional ESNs or IT<br>services companies.</p></div>
  <div class="benefit" style="left:790px;top:596px"><div class="benefit__art" role="img" aria-label="Sketch of a team building together"></div><p>Co-build your digital<br>projects of tomorrow with<br>a committed team.</p></div>
</section>

<section class="abs who">
  <h2>WHO WE ARE</h2>
  <div class="who__text">
    <p>BRIGHTVALE.COOP is a cooperative and participatory company specializing in digital services.</p>
    <p>Lorem ipsum dolor sit amet, consectetur adipiscing elit, sed do eiusmod tempor incididunt ut labore et dolore magna aliqua ipsum suspendisse ultrices gravida.</p>
  </div>
  <a class="btn btn--outline-dark" style="left:144px;top:371px;width:181px">Contact us <svg viewBox="0 0 16 16"><circle cx="8" cy="8" r="8" fill="#0c3b3a"/><path d="M6.5 4.5 10 8l-3.5 3.5" stroke="#fff" stroke-width="2.2" fill="none"/></svg></a>
  <a class="btn btn--teal" style="left:338px;top:371px;width:181px">Watch video <svg viewBox="0 0 16 16"><circle cx="8" cy="8" r="8" fill="#fff"/><path d="M6.5 4.5 10 8l-3.5 3.5" stroke="#1aa7b4" stroke-width="2.2" fill="none"/></svg></a>
  <div class="video" role="img" aria-label="Video cover illustration of characters in a small town">
    <svg class="play" width="70" height="70" viewBox="0 0 70 70"><circle cx="35" cy="35" r="34" fill="#111"/><circle cx="35" cy="35" r="30" fill="none" stroke="#fff" stroke-width="2"/><path d="M27 20v30l24-15z" fill="#fff"/></svg>
  </div>
</section>

<section class="abs contact">
  <h2 class="section-title">CONTACT US</h2>
  <h3 style="left:144px">CONTACT FORM</h3>
  <p class="note" style="left:144px;top:276px">By email at contact@brightvale.coop or via this form</p>
  <div class="field" style="top:326px;height:51px">Enter Name</div>
  <div class="field" style="top:393px;height:51px">Enter Email</div>
  <div class="field" style="top:460px;height:88px">Message</div>
  <a class="btn btn--teal" style="left:144px;top:574px;width:141px">Submit <svg viewBox="0 0 16 16"><circle cx="8" cy="8" r="8" fill="#fff"/><path d="M6.5 4.5 10 8l-3.5 3.5" stroke="#1aa7b4" stroke-width="2.2" fill="none"/></svg></a>

  <h3 style="left:651px">FIND US</h3>
  <div class="info" style="top:268px"><svg viewBox="0 0 16 16"><path d="M3 1h3l1.5 4-2 1.5a9 9 0 0 0 4 4L11 8.5l4 1.5v3a2 2 0 0 1-2 2A12 12 0 0 1 1 3a2 2 0 0 1 2-2z" fill="#1aa7b4"/></svg>Phone: 01 47 20 65 13</div>
  <div class="info" style="top:303px"><svg viewBox="0 0 16 16"><path d="M8 0a5.5 5.5 0 0 0-5.5 5.5C2.5 10 8 16 8 16s5.5-6 5.5-10.5A5.5 5.5 0 0 0 8 0zm0 8a2.5 2.5 0 1 1 0-5 2.5 2.5 0 0 1 0 5z" fill="#1aa7b4"/></svg>BRIGHTVALE.COOP - HALLWORKS -<br>18 Rue des Tanneurs 75011 Paris</div>
  <div class="map" role="img" aria-label="Street map of the Paris 11th district showing the office location"></div>
</section>

<footer class="abs footer">
  <div class="brand brand--foot">BRIGHTVALE<small>.COOP</small></div>
  <p class="copy">© 2020 Brightvale.coop . All Rights reserved &nbsp;|&nbsp; Privacy</p>
  <div class="social" aria-label="Social links"><span></span><span></span><span></span></div>
</footer>

</body>
</html>
```